post card 4x6

this is a post card that will be sent to plumbing companies and foundation repair companies for whole sale work. if you can add ( work done in unmarked truck -will ware your shirt)

```html
<!DOCTYPE html>
<html lang="en">
<head>
<meta charset="utf-8">
<title>DrainLine Postcard 4x6</title>
<link rel="stylesheet" href="https://fonts.googleapis.com/css2?family=Poppins:wght@300;400;500;600;700;800&display=swap">
<style>
:root{
  --navy:#2b3445;
  --navy-deep:#232a38;
  --red:#e84c43;
  --red-dark:#c23a32;
  --white:#ffffff;
  --paper:#f4f4f4;
  --stamp:#dcdcdc;
  --rule:#9a9a9a;
}
*{margin:0;padding:0;box-sizing:border-box}
html,body{width:1200px;height:2400px;overflow:hidden;background:var(--white);font-family:"Poppins",sans-serif}
.canvas{position:relative;width:1200px;height:2400px}
.card{position:absolute;left:50px;width:1100px;height:733px;overflow:hidden;box-shadow:0 2px 10px rgba(0,0,0,.25)}
.card--front{top:417px;background:var(--navy)}
.card--back{top:1216px;background:var(--white)}

/* front */
.hero-panel{position:absolute;left:0;top:0;width:550px;height:400px;background:var(--navy);padding:60px 0 0 69px;color:var(--white)}
.brand{font-family:"Poppins",sans-serif;font-weight:800;color:var(--red);line-height:1;letter-spacing:1px}
.hero-panel .brand{font-size:52px;margin-bottom:30px}
.headline-intro{font-size:33px;font-weight:300;line-height:1}
.headline-sub{font-size:33px;font-weight:700;line-height:1;margin-bottom:12px}
.headline-main{font-size:52px;font-weight:800;line-height:1;color:var(--red)}
.headline-main.white{color:var(--white)}
.hero-photo{position:absolute;left:550px;top:0;width:550px;height:400px;background:linear-gradient(160deg,#eceae6 0%,#c9c6c0 45%,#3a4fa8 75%,#dcdad6 100%)}
.intro-band{position:absolute;left:0;top:400px;width:550px;height:98px;background:var(--red);color:var(--white);font-size:21px;line-height:1.18;font-weight:400;padding:10px 0 0 69px}
.truck-band{position:absolute;left:550px;top:400px;width:550px;height:98px;background:var(--navy);padding:18px 0 0 26px;font-weight:800;font-size:28px;line-height:1;color:var(--white)}
.truck-band span{display:block;color:var(--red)}
.feature-row{position:absolute;left:0;top:498px;width:1100px;height:122px;background:var(--white);display:flex;align-items:center}
.feature{flex:1;display:flex;align-items:center;gap:14px;padding-left:60px;height:78px;border-right:2px solid #d5d5d5}
.feature:last-child{border-right:none}
.feature-icon{width:70px;height:70px;flex:none}
.feature-text{font-size:21px;font-weight:500;line-height:1.2;color:var(--navy)}
.front-footer{position:absolute;left:0;top:620px;width:1100px;height:113px}
.footer-shape{position:absolute;left:0;top:0}
.call{position:absolute;display:flex;align-items:center;color:var(--white);font-weight:700;white-space:nowrap}
.call .call-label{margin-right:30px}
.call .phone{display:flex;align-items:center;gap:8px}
.phone-icon{flex:none}
.front-footer .call{left:64px;top:14px;font-size:42px}
.url{position:absolute;color:var(--white);font-weight:600;white-space:nowrap}
.url em{font-style:normal;color:var(--red)}
.front-footer .url{left:718px;top:48px;font-size:22px;letter-spacing:.3px}

/* back */
.services-panel{position:absolute;left:0;top:0;width:583px;height:733px;background:var(--navy);color:var(--white);padding:46px 0 0 59px}
.services-title{font-size:40px;font-weight:400;line-height:1}
.services-title strong{font-weight:700;color:var(--red)}
.services-copy{margin-top:22px;width:480px;font-size:18px;line-height:1.17;font-weight:400}
.services-copy strong{color:var(--red);font-weight:700}
.service-photos{display:flex;gap:7px;margin-top:15px}
.service-photo{width:158px;height:110px}
.service-photo--burst{background:linear-gradient(135deg,#5b5048,#9a9590 55%,#3c3a38)}
.service-photo--jet{background:linear-gradient(135deg,#b8bcc0,#eef0f2 55%,#8d9399)}
.service-photo--camera{background:linear-gradient(135deg,#d8d3cc,#f3f0ec 45%,#6b5a4a)}
.service-list{display:grid;grid-template-columns:240px 270px;margin-top:24px}
.service-list ul{list-style:none}
.service-list li{display:flex;align-items:flex-start;gap:14px;font-size:18px;font-weight:600;line-height:1.17;margin-bottom:20px;white-space:nowrap}
.service-list li svg{flex:none;margin-top:3px}
.back-call{position:absolute;left:0;top:563px;width:623px;height:170px}
.back-call .call{left:29px;top:14px;font-size:36px}
.back-call .url{left:29px;top:90px;font-size:32px;letter-spacing:.5px}
.address-side .brand{position:absolute;left:624px;top:50px;font-size:42px}
.stamp-box{position:absolute;left:910px;top:50px;width:128px;height:156px;background:var(--stamp)}
.address-line{position:absolute;left:624px;width:411px;height:2px;background:var(--rule)}
</style>
</head>
<body>
<div class="canvas">

  <section class="card card--front" aria-label="Postcard front">
    <div class="hero-panel">
      <div class="brand">DrainLine</div>
      <p class="headline-intro">YOUR ONE-STOP</p>
      <p class="headline-sub">SOLUTION FOR</p>
      <p class="headline-main">PLUMBING &amp;</p>
      <p class="headline-main">IRRIGATION</p>
      <p class="headline-main white">INSTALLATION</p>
    </div>
    <div class="hero-photo" role="img" aria-label="Photo of a plumber in blue overalls repairing pipes under a kitchen sink"></div>
    <div class="intro-band">DrainLine Plumbing is Bexar County's Leader in Hydro Jetting, Trenchless Plumbing, and Pipe Repair for your home or business.</div>
    <div class="truck-band">WORK DONE IN UNMARKED TRUCK<span>-WILL WARE YOUR SHIRT</span></div>

    <div class="feature-row">
      <div class="feature">
        <svg class="feature-icon" viewBox="0 0 70 70"><circle cx="35" cy="35" r="34" fill="none" stroke="#e84c43" stroke-width="1.5" stroke-dasharray="3 2"/><circle cx="35" cy="35" r="29" fill="#2b3445"/><rect x="22" y="27" width="26" height="20" rx="4" fill="none" stroke="#fff" stroke-width="2.5"/><path d="M29 32v10M35 30v12M41 32v10" stroke="#fff" stroke-width="2.5"/><circle cx="35" cy="21" r="3" fill="#e84c43"/></svg>
        <p class="feature-text">Fast &amp; Reliable<br>Drain Cleaning</p>
      </div>
      <div class="feature">
        <svg class="feature-icon" viewBox="0 0 70 70"><circle cx="35" cy="35" r="34" fill="none" stroke="#e84c43" stroke-width="1.5" stroke-dasharray="3 2"/><circle cx="35" cy="35" r="29" fill="#2b3445"/><path d="M18 40h10v-8h14v8h10M28 32v-6h14v6M35 20v6" fill="none" stroke="#fff" stroke-width="2.5"/><rect x="16" y="37" width="4" height="8" fill="#fff"/><rect x="50" y="37" width="4" height="8" fill="#fff"/><circle cx="35" cy="48" r="2.5" fill="#e84c43"/></svg>
        <p class="feature-text">Certified Pipe<br>Lining Services</p>
      </div>
      <div class="feature">
        <svg class="feature-icon" viewBox="0 0 70 70"><circle cx="35" cy="35" r="34" fill="none" stroke="#e84c43" stroke-width="1.5" stroke-dasharray="3 2"/><circle cx="35" cy="35" r="29" fill="#2b3445"/><path d="M24 20v10a11 11 0 0 0 22 0V20" fill="none" stroke="#fff" stroke-width="3"/><path d="M35 41v10" stroke="#fff" stroke-width="3"/><path d="M20 20h8M42 20h8" stroke="#fff" stroke-width="3"/><path d="M46 28l5 -3M46 33l6 1" stroke="#e84c43" stroke-width="2.5"/></svg>
        <p class="feature-text">Emergency Pipe<br>Burst Repair</p>
      </div>
    </div>

    <div class="front-footer">
      <svg class="footer-shape" width="1100" height="113" viewBox="0 0 1100 113">
        <rect width="1100" height="113" fill="#2b3445"/>
        <polygon points="0,0 1100,0 1100,22 720,22 650,96 0,96" fill="#e84c43"/>
        <polygon points="650,96 720,22 732,22 660,104 0,104 0,96" fill="#ffffff"/>
      </svg>
      <div class="call"><span class="call-label">Call Us Now!</span><span class="phone"><svg class="phone-icon" width="30" height="30" viewBox="0 0 30 30"><circle cx="15" cy="15" r="12" fill="none" stroke="#fff" stroke-width="2.5"/><path d="M10 9c0 7 4 11 11 11l1.5-3-3-1.5-1.5 1.5c-2-1-3.5-2.5-4.5-4.5l1.5-1.5L13.5 8z" fill="#fff"/></svg>877-555-0142</span></div>
      <div class="url">www.<em>drainlineplumbing</em>.com</div>
    </div>
  </section>

  <section class="card card--back" aria-label="Postcard back">
    <div class="services-panel">
      <h2 class="services-title">OUR <strong>SERVICES</strong></h2>
      <p class="services-copy">We are proud to serve <strong>the Southern California area, primarily Bexar County and it's surrounding cities.</strong> We have been servicing Bexar County since 1998 and are proud to call it our home. We handle everything from drain repair and cleaning, pipe lining, pipe bursting, trenchless sewer repair, and we use sewer video inspection to know exactly what is going on in your pipes.</p>
      <div class="service-photos">
        <div class="service-photo service-photo--burst" role="img" aria-label="Photo of a pipe bursting head in soil"></div>
        <div class="service-photo service-photo--jet" role="img" aria-label="Photo of a hydro jetting nozzle spraying water"></div>
        <div class="service-photo service-photo--camera" role="img" aria-label="Photo of a technician running a sewer camera inspection"></div>
      </div>
      <div class="service-list">
        <ul>
          <li><svg width="14" height="14" viewBox="0 0 14 14"><circle cx="7" cy="7" r="7" fill="#e84c43"/><path d="M4 7.2l2 2 4-4" fill="none" stroke="#fff" stroke-width="1.6"/></svg>Pipe Bursting</li>
          <li><svg width="14" height="14" viewBox="0 0 14 14"><circle cx="7" cy="7" r="7" fill="#e84c43"/><path d="M4 7.2l2 2 4-4" fill="none" stroke="#fff" stroke-width="1.6"/></svg>Pipe Lining</li>
          <li><svg width="14" height="14" viewBox="0 0 14 14"><circle cx="7" cy="7" r="7" fill="#e84c43"/><path d="M4 7.2l2 2 4-4" fill="none" stroke="#fff" stroke-width="1.6"/></svg>Sewer Video Inspection</li>
        </ul>
        <ul>
          <li><svg width="14" height="14" viewBox="0 0 14 14"><circle cx="7" cy="7" r="7" fill="#e84c43"/><path d="M4 7.2l2 2 4-4" fill="none" stroke="#fff" stroke-width="1.6"/></svg>Drain and Pipe Repair<br>and Cleaning</li>
          <li><svg width="14" height="14" viewBox="0 0 14 14"><circle cx="7" cy="7" r="7" fill="#e84c43"/><path d="M4 7.2l2 2 4-4" fill="none" stroke="#fff" stroke-width="1.6"/></svg>Hydro Jetting</li>
        </ul>
      </div>
    </div>

    <div class="back-call">
      <svg class="footer-shape" width="623" height="170" viewBox="0 0 623 170">
        <rect x="0" y="73" width="583" height="97" fill="#2b3445"/>
        <polygon points="583,73 623,36 583,110" fill="#c23a32"/>
        <polygon points="0,0 583,0 623,36 583,73 0,73" fill="#e84c43"/>
      </svg>
      <div class="call"><span class="call-label">Call Us Now!</span><span class="phone"><svg class="phone-icon" width="26" height="26" viewBox="0 0 30 30"><circle cx="15" cy="15" r="12" fill="none" stroke="#fff" stroke-width="2.5"/><path d="M10 9c0 7 4 11 11 11l1.5-3-3-1.5-1.5 1.5c-2-1-3.5-2.5-4.5-4.5l1.5-1.5L13.5 8z" fill="#fff"/></svg>877-555-0142</span></div>
      <div class="url">www.<em>drainlineplumbing</em>.com</div>
    </div>

    <div class="address-side">
      <div class="brand">DrainLine</div>
      <div class="stamp-box"></div>
      <div class="address-line" style="top:243px"></div>
      <div class="address-line" style="top:316px"></div>
      <div class="address-line" style="top:387px"></div>
      <div class="address-line" style="top:459px"></div>
    </div>
  </section>

</div>
</body>
</html>
```